Redesign of business card for Cedar Ridge Mechanical

We are looking for a new design for our business cards for Cedar Ridge Mechanical. We are a plumbing & HVAC construction company, operating on the West Coast of Canada and USA. Logo attached.
Industry/Entity Type
Construction - Plumbing & HVAC
Contact Information for Business Card
Name, address, phone numbers, email, website address
Look and feel
Each slider illustrates characteristics of the customer's brand and the style your logo design should communicate.

```html
<!DOCTYPE html>
<html lang="en">
<head>
<meta charset="UTF-8">
<title>Cedar Ridge Mechanical – Business Card</title>
<link href="https://fonts.googleapis.com/css2?family=Poppins:wght@300;400;700&display=swap" rel="stylesheet">
<style>
  :root {
    --backdrop: #1f1f21;
    --card: #232325;
    --ink: #ffffff;
    --ink-soft: #d9d9d9;
    --rule: #8a8a8c;
  }
  * { margin: 0; padding: 0; box-sizing: border-box; }
  html, body {
    width: 1200px; height: 711px; overflow: hidden;
    background: var(--backdrop);
    font-family: "Poppins", sans-serif;
    color: var(--ink);
  }
  .stage { position: relative; width: 1200px; height: 711px; }
  .card {
    position: absolute; top: 200px;
    width: 540px; height: 309px;
    background: var(--card);
    box-shadow: 0 14px 30px rgba(0,0,0,.55);
    overflow: hidden;
  }
  .card--front { left: 40px; }
  .card--back { left: 620px; }
  .edge-bar { position: absolute; width: 9px; background: var(--ink); }
  .card--front .edge-bar--top { right: 44px; top: 0; height: 92px; }
  .card--front .edge-bar--bottom { left: 44px; bottom: 0; height: 112px; }
  .card--back .edge-bar--top { right: 22px; top: 0; height: 118px; }
  .card--back .edge-bar--bottom { left: 22px; bottom: 0; height: 132px; }

  .brand { position: absolute; display: flex; align-items: center; gap: 12px; }
  .brand__mark { background: var(--ink); flex: none; }
  .brand__name {
    font-weight: 700; text-transform: uppercase; line-height: 1.05;
    letter-spacing: .06em;
  }
  .card--front .brand { left: 128px; top: 118px; }
  .card--front .brand__mark { width: 58px; height: 58px; }
  .card--front .brand__name { font-size: 25px; }
  .card--back .brand { left: 58px; top: 136px; gap: 9px; }
  .card--back .brand__mark { width: 34px; height: 34px; }
  .card--back .brand__name { font-size: 14px; }

  .divider {
    position: absolute; left: 236px; top: 84px;
    width: 1px; height: 150px; background: var(--rule);
  }
  .person { position: absolute; left: 268px; top: 66px; }
  .person__name { font-size: 26px; line-height: 1.1; }
  .person__first { font-weight: 700; }
  .person__last { font-weight: 300; }
  .person__title { font-size: 12px; font-weight: 400; color: var(--ink-soft); margin-top: 2px; }
  .contacts { list-style: none; margin-top: 20px; }
  .contacts li {
    display: flex; align-items: center; gap: 9px;
    font-size: 12.5px; font-weight: 300; line-height: 1; margin-bottom: 8px;
  }
  .contacts svg { width: 13px; height: 13px; flex: none; }
  .address {
    position: absolute; left: 0; right: 0; bottom: 30px;
    text-align: center; font-size: 13px; font-weight: 300; letter-spacing: .01em;
  }
</style>
</head>
<body>
<main class="stage">
  <section class="card card--front" aria-label="Business card front">
    <span class="edge-bar edge-bar--top"></span>
    <span class="edge-bar edge-bar--bottom"></span>
    <div class="brand">
      <span class="brand__mark"></span>
      <span class="brand__name">Cedar Ridge<br>Mechanical</span>
    </div>
  </section>

  <section class="card card--back" aria-label="Business card back">
    <span class="edge-bar edge-bar--top"></span>
    <span class="edge-bar edge-bar--bottom"></span>
    <div class="brand">
      <span class="brand__mark"></span>
      <span class="brand__name">Cedar Ridge<br>Mechanical</span>
    </div>
    <span class="divider"></span>
    <div class="person">
      <p class="person__name"><span class="person__first">Marta</span> <span class="person__last">Kovale</span></p>
      <p class="person__title">Founder &amp; CEO</p>
      <ul class="contacts">
        <li>
          <svg viewBox="0 0 24 24" fill="#fff" aria-hidden="true"><path d="M6.6 10.8a15.1 15.1 0 0 0 6.6 6.6l2.2-2.2c.3-.3.7-.4 1-.2 1.1.4 2.3.6 3.6.6.6 0 1 .4 1 1V20c0 .6-.4 1-1 1A17 17 0 0 1 3 4c0-.6.4-1 1-1h3.5c.6 0 1 .4 1 1 0 1.3.2 2.5.6 3.6.1.3 0 .7-.2 1z"/></svg>
          (604) 555-0182
        </li>
        <li>
          <svg viewBox="0 0 24 24" fill="none" stroke="#fff" stroke-width="2" aria-hidden="true"><circle cx="12" cy="12" r="9"/><path d="M3 12h18M12 3c3 3 3 15 0 18M12 3c-3 3-3 15 0 18"/></svg>
          info@cedarridgemech.com
        </li>
        <li>
          <svg viewBox="0 0 24 24" fill="none" stroke="#fff" stroke-width="2" aria-hidden="true"><rect x="3" y="5" width="18" height="14"/><path d="M3 6l9 7 9-7"/></svg>
          www.cedarridgemech.com
        </li>
      </ul>
    </div>
    <p class="address">1840 Harbor View Rd. Suite 310 Vancouver, BC V6B 2K9</p>
  </section>
</main>
</body>
</html>
```